Design a New Business Card for Our Company

We are looking for fresh, unique, and a modern business card that reflects our roots as digital marketing agency focused on SEM.

Industry/Entity Type

Marketing

Contact Information for Business Card

looking for very unique out of the box designs. clean and modern that compliments our logo

Requirements
Must have
• colors should match our logo
• Front should have name, address, email, and phone/fax of the person, phone/fax are the same number
• back should have our url

```html
<!DOCTYPE html>
<html lang="en">
<head>
<meta charset="utf-8">
<title>Clearpath Solutions – Business Card</title>
<link rel="stylesheet" href="https://fonts.googleapis.com/css2?family=Open+Sans:wght@400;600;700&display=swap">
<style>
  :root {
    --brand-blue: #5b97d1;
    --brand-blue-deep: #4d88c4;
    --brand-grey: #a9a9ab;
    --band-grey: #b3b3b3;
    --paper: #ffffff;
    --stage: #ececec;
    --ink-light: #ffffff;
  }
  * { margin: 0; padding: 0; box-sizing: border-box; }
  html, body {
    width: 1200px; height: 900px; overflow: hidden;
    background: var(--stage);
    font-family: "Open Sans", Arial, sans-serif;
  }
  .canvas { position: relative; width: 1200px; height: 900px; }

  .card { position: absolute; overflow: hidden; box-shadow: 0 6px 18px rgba(0,0,0,.15); }

  /* Front */
  .card-front { left: 77px; top: 34px; width: 589px; height: 363px; background: var(--paper); }
  .front-bands { position: absolute; left: 0; top: 0; }
  .company-name { position: absolute; white-space: nowrap; line-height: 1; }
  .card-front .company-name {
    left: 0; right: 0; top: 82px; text-align: center;
    color: var(--brand-grey); font-size: 42px; font-weight: 600;
  }
  .contact-list { position: absolute; right: 323px; top: 247px; list-style: none; color: var(--ink-light); font-size: 15px; line-height: 24px; text-align: right; }
  .contact-list li { display: flex; justify-content: flex-end; align-items: center; gap: 8px; }
  .contact-list svg { width: 12px; height: 12px; fill: var(--ink-light); }
  .person { position: absolute; left: 302px; top: 230px; color: var(--ink-light); }
  .person-name { font-size: 20px; font-weight: 600; line-height: 26px; }
  .person-role { font-size: 15px; line-height: 20px; }
  .person-address { font-size: 15px; line-height: 19px; margin-top: 13px; }

  /* Back */
  .card-back { left: 389px; top: 505px; width: 566px; height: 352px; background: var(--brand-blue); }
  .back-pattern { position: absolute; inset: 0; background: radial-gradient(circle at 40% 45%, var(--brand-blue) 0%, var(--brand-blue-deep) 100%); }
  .card-back .company-name {
    right: 42px; top: 205px;
    color: var(--ink-light); font-size: 40px; font-weight: 700;
  }
  .website { position: absolute; right: 97px; bottom: 30px; color: var(--ink-light); font-size: 16px; font-weight: 700; }
</style>
</head>
<body>
<main class="canvas">

  <section class="card card-front" aria-label="Business card front">
    <svg class="front-bands" width="589" height="363" viewBox="0 0 589 363" aria-hidden="true">
      <polygon points="0,182 400,182 386,209 0,209" fill="var(--band-grey)"/>
      <polygon points="0,211 386,211 414,175 589,175 589,363 0,363" fill="var(--brand-blue)"/>
    </svg>

    <p class="company-name">Clearpath Solutions</p>

    <ul class="contact-list">
      <li>(041)-382-5170
        <svg viewBox="0 0 12 12"><path d="M2.5 1l2 2-1 1.3c.6 1.4 1.7 2.5 3.2 3.2l1.3-1 2 2-1.3 1.5C5.8 10 2 6.2 1 2.3z"/></svg>
      </li>
      <li>138-382-5170
        <svg viewBox="0 0 12 12"><path d="M3 1h5v3H3zM1 5h10v6H1zm2 2v1h2V7zm4 0v1h2V7z"/></svg>
      </li>
      <li>hello@clearpath.co
        <svg viewBox="0 0 12 12"><path d="M1 2.5h10v7H1zm1 1v.4l4 2.6 4-2.6v-.4z"/></svg>
      </li>
    </ul>

    <div class="person">
      <p class="person-name">Daniel Carter</p>
      <p class="person-role">Managing Director</p>
      <p class="person-address">48 Harbour Lane, Suite 210<br>Westbridge, 560218</p>
    </div>
  </section>

  <section class="card card-back" aria-label="Business card back">
    <div class="back-pattern" role="img" aria-label="Scattered soft blue circles pattern"></div>
    <p class="company-name">Clearpath Solutions</p>
    <p class="website">www.clearpath.co</p>
  </section>

</main>
</body>
</html>
```